Personal letterhead and stationary

I am looking for someone to design letterhead and stationary set for my personal use. I want something simple and timeless with a little bit of color. I like photography, computers and writing.

```html
<!DOCTYPE html>
<html lang="en">
<head>
<meta charset="UTF-8">
<title>Theodore Jay Walsh – Letterhead</title>
<link rel="stylesheet" href="https://fonts.googleapis.com/css2?family=Josefin+Slab:wght@300;400;600&family=Libre+Baskerville:wght@700&display=swap">
<style>
  :root {
    --ink: #1e1e1e;
    --ink-soft: #555555;
    --rule: #9a9a9a;
    --paper: #ffffff;
  }
  html, body {
    margin: 0;
    padding: 0;
    overflow: hidden;
    background: var(--paper);
  }
  .letterhead {
    position: relative;
    width: 849px;
    height: 1200px;
    background: var(--paper);
    color: var(--ink);
    font-family: "Josefin Slab", serif;
    overflow: hidden;
  }
  .sender-name {
    position: absolute;
    left: 83px;
    top: 108px;
    margin: 0;
    width: 262px;
    white-space: nowrap;
    font-size: 22px;
    line-height: 26px;
    font-weight: 400;
    letter-spacing: 0.5px;
    text-transform: uppercase;
  }
  .sender-email {
    position: absolute;
    left: 83px;
    top: 160px;
    font-size: 14px;
    font-weight: 300;
    color: var(--ink-soft);
  }
  .sender-phone {
    position: absolute;
    right: 68px;
    top: 108px;
    display: flex;
    align-items: center;
    gap: 6px;
    font-size: 20px;
    font-weight: 300;
    font-style: italic;
  }
  .sender-phone svg { width: 20px; height: 20px; }
  .sender-address {
    position: absolute;
    right: 68px;
    top: 160px;
    font-size: 14px;
    font-weight: 300;
    color: var(--ink-soft);
  }
  .header-rule {
    position: absolute;
    top: 186px;
    height: 1px;
    background: var(--rule);
  }
  .header-rule.left { left: 83px; width: 260px; }
  .header-rule.right { left: 506px; width: 275px; }
  .brand-mark {
    position: absolute;
    left: 358px;
    top: 72px;
    width: 132px;
    height: 132px;
    border: 2px solid var(--ink);
    border-radius: 50%;
    display: flex;
    align-items: center;
    justify-content: center;
    font-size: 22px;
    line-height: 1;
    font-weight: 400;
    letter-spacing: 2px;
    box-sizing: border-box;
    background: var(--paper);
  }
  .letter-body {
    position: absolute;
    left: 0;
    top: 540px;
    width: 100%;
    text-align: center;
    font-size: 33px;
    font-weight: 300;
    line-height: 46px;
    letter-spacing: 1.5px;
    margin: 0;
  }
  .footer-rule {
    position: absolute;
    left: 83px;
    width: 683px;
    top: 1122px;
    height: 1px;
    background: var(--rule);
  }
  .footer-quote {
    position: absolute;
    left: 0;
    top: 1131px;
    width: 100%;
    text-align: center;
    font-family: "Libre Baskerville", serif;
    font-weight: 700;
    font-size: 11px;
    line-height: 16px;
    margin: 0;
  }
</style>
</head>
<body>
<div class="letterhead">
  <h1 class="sender-name">Theodore Jay Walsh</h1>
  <div class="sender-email">theo.walsh@postmail.com.au</div>

  <div class="header-rule left"></div>
  <div class="brand-mark">WALSH</div>
  <div class="header-rule right"></div>

  <div class="sender-phone">
    <svg viewBox="0 0 24 24" aria-hidden="true">
      <path fill="#1e1e1e" d="M6.6 10.8c1.4 2.8 3.8 5.1 6.6 6.6l2.2-2.2c.3-.3.7-.4 1-.2 1.1.4 2.3.6 3.6.6.6 0 1 .4 1 1V20c0 .6-.4 1-1 1C10.6 21 3 13.4 3 4c0-.6.4-1 1-1h3.5c.6 0 1 .4 1 1 0 1.3.2 2.5.6 3.6.1.3 0 .7-.2 1L6.6 10.8z"/>
    </svg>
    <span>0412 508 316</span>
  </div>
  <div class="sender-address">14 linden st ashford vic 3190</div>

  <p class="letter-body">
    Hi please use<br>
    the Vellum Core Roman<br>
    you can find the font on Fontshelf
  </p>

  <div class="footer-rule"></div>
  <p class="footer-quote">
    Be the change you want to see in the World<br>
    -Arjun Mehra
  </p>
</div>
</body>
</html>
```